Tusk Hollow Lodge website (design only)

Tusk Hollow Lodge (http://www.tuskhollowlodge-mw.example) is a private Safari lodge located in Malawi.
We would like a modern, professional website designed that does not subscribe to the cliched view of a Safari in Africa, but still maintain a wildlife/safari atmosphere.

The aim of our website is to entice people & drive them to the booking form.

Here are some examples of websites that we like. Although we would like our site to be a bit more in line with modern web design trends.

http://www.marulaplains.example/
http://www.kovunde.example/
http://www.tembalorecamp.example/

Requirements
Must have
• Here is a list of the pages required. Most of them will follow a standard content layout. I.e. heading, body and images.

If you take a look at the website, you will get an idea of hoe many page types there are +- 5

http://www.tuskhollowlodge-mw.example/index.htm

About Tusk Hollow
Lirundu Country Club
Rooms
Conferences
Cuisine
Facilities
Your Safari
Activities
Rates & Special Offers
Booking form
Latest Developments
How To Get There
Gallery
Contact Us
Blog / Newsfeed

```html
<!DOCTYPE html>
<html lang="en">
<head>
<meta charset="utf-8">
<title>Tusk Hollow Lodge</title>
<link rel="stylesheet" href="https://fonts.googleapis.com/css2?family=Carlito:ital,wght@0,400;0,700;1,400&display=swap">
<style>
:root{
  --band:#c2ae8c;
  --page:#ecd6a7;
  --panel:#ae9b78;
  --panel-edge:#8a7653;
  --nav:#c9b48f;
  --ink:#3a3020;
  --ink-soft:#4a3e2a;
  --white:#ffffff;
  --shadow:rgba(70,55,30,.35);
}
*{margin:0;padding:0;box-sizing:border-box}
html,body{width:1152px;height:1200px;overflow:hidden}
body{background:var(--page);font-family:"Carlito",Calibri,sans-serif;color:var(--ink);position:relative}
.site-header{position:absolute;left:0;top:0;width:1152px;height:108px;background:var(--band)}
.brand{position:absolute;left:124px;top:10px;font-weight:700;font-size:40px;letter-spacing:.5px;color:var(--white)}
.tagline{position:absolute;left:125px;top:58px;font-size:22px;letter-spacing:1px;color:var(--white)}
.hero{position:absolute;left:126px;top:127px;width:672px;height:287px;border-radius:4px;box-shadow:0 2px 6px var(--shadow);background:linear-gradient(180deg,#4f6a2a 0%,#7d9a3c 55%,#9ab43e 80%,#7f9a35 100%)}
.welcome{position:absolute;left:125px;top:439px;width:673px;height:487px;background:var(--panel);border-radius:4px;box-shadow:0 2px 6px var(--shadow);padding:12px 15px}
.welcome h1{font-size:18px;font-weight:700;color:var(--white);margin-bottom:10px}
.welcome p{font-size:13.2px;line-height:17.8px;margin-bottom:16px}
.welcome p.lead{font-style:italic}
.promo{position:absolute;top:944px;height:144px;border-radius:4px;box-shadow:0 2px 6px var(--shadow);overflow:hidden}
.promo-functions{left:126px;width:324px;background:linear-gradient(180deg,#c7d6e0 0%,#9aa771 40%,#6f9a3a 70%,#7aa23e 100%)}
.promo-booking{left:474px;width:324px;background:linear-gradient(180deg,#c9d3d8 0%,#aab5b2 60%,#8e9a84 100%)}
.promo-functions .caption{position:absolute;left:0;right:0;bottom:10px;text-align:center;color:var(--white);font-weight:700;font-size:14px;line-height:20px;text-shadow:1px 1px 2px #222}
.promo-booking .caption{position:absolute;left:11px;top:6px;color:#fff8e8;font-weight:700;font-size:20px;line-height:32px;text-shadow:1px 1px 2px #3b3020}
.main-nav{position:absolute;left:817px;top:109px;width:210px;height:426px;background:var(--nav);border-radius:0 0 8px 8px;box-shadow:0 3px 6px var(--shadow);padding-top:10px}
.main-nav ul{list-style:none}
.main-nav li{height:27px;line-height:27px;padding-left:48px;font-size:14.5px;color:var(--ink-soft);position:relative}
.main-nav li::before{content:"»";position:absolute;left:28px;font-size:12px}
.main-nav li.current{background:linear-gradient(90deg,rgba(255,255,255,.2),#f3ead8 60%,rgba(255,255,255,.3));color:var(--ink);margin-right:12px;border-radius:0 3px 3px 0}
.updates{position:absolute;left:817px;top:541px;width:210px;height:547px;background:var(--panel);border-radius:4px;box-shadow:0 2px 6px var(--shadow);padding:8px 10px}
.updates h2{font-size:17px;font-weight:700;color:var(--white);margin-bottom:12px}
.updates h3{font-size:12.5px;font-style:italic;font-weight:400;margin-bottom:3px}
.updates p{font-size:11px;line-height:13.5px}
.updates .more{display:block;text-align:right;color:var(--white);font-size:11px;margin:12px 0 24px}
.site-footer{position:absolute;left:0;top:1119px;width:1152px;height:81px;background:var(--band);box-shadow:0 -3px 5px var(--shadow)}
.site-footer p{text-align:center;color:var(--white);font-size:10.5px;font-weight:700;margin-top:23px}
</style>
</head>
<body>
<header class="site-header">
  <div class="brand">Tusk Hollow Lodge</div>
  <div class="tagline">Kalinde Estate Nsaleni</div>
</header>

<div class="hero" role="img" aria-label="Two waterbuck standing on a grassy clearing before green bush"></div>

<section class="welcome">
  <h1>Welcome to Tusk Hollow Lodge</h1>
  <p>Warmest welcome to the unique Malawi experience. lodge complex, game park, the 18 hole Lirundu golf club and Nkhuzi dam.</p>
  <p class="lead">A multi million dollar development at Kalinde estate, Nsaleni on Kasimba road 20 kms from Matemba Malawi's commercial capital creating a fascinating paradise for multiple leisure activities and conserving Malawi wildlife.Our Lodge also has beautifully designed and built in golden colored rock.</p>
  <p>The 1st phase was completed in 2007, and is approx 1800 sq. meters, comprising of:<br>A fully carpeted and elegantly furnished restaurant with seating for up to 80 guests and exceptional cuisine to completely satisfy most palates.</p>
  <p>A stately carpeted conference hall for up to 45 people, 5 luxurious and spacious ensuite cottages with lounge and private verandah accessing a beautiful 18 meter swimming pool with cascading waterfall.<br>The entire Kalinde estate comprises of 220 hectares of exquisite, undulating indigenous forest and grassland and is protected by an 8 km perimeter road enclosed by a 3 meter high game fence on either side of the road .<br>There are at least 40 kms of dirt roads and numerous paths for drives and walks, the most beautiful of which is along the Kalinde stream which dissects the property.</p>
  <p>Tusk Hollow Lodge is situated 2 kms off the Kasimba road and is only 22kms from Malawi's commercial capital Matemba and 12 kms from its suburb of Chisanga.</p>
  <p>Although so conveniently close to town tusk hollow lodge provides all the holiday and business prerequisites in a beautiful, relaxing, quiet and secure environment.</p>
</section>

<div class="promo promo-functions" role="img" aria-label="Brick lodge buildings with green roofs on a lawn">
  <div class="caption">Game Sanctuary.....All Corporate and Private<br>Functions..... Holiday Retreat</div>
</div>
<div class="promo promo-booking" role="img" aria-label="A giraffe against hazy hills">
  <div class="caption">ENQUIRE<br>FOR A<br>BOOKING</div>
</div>

<nav class="main-nav">
  <ul>
    <li class="current">About Tusk Hollow</li>
    <li>Lirundu Country Club</li>
    <li>Rooms</li>
    <li>Conferences</li>
    <li>Cuisine</li>
    <li>Facilities</li>
    <li>Your Safari</li>
    <li>Activities</li>
    <li>Rates &amp; Special Offers</li>
    <li>Booking requests</li>
    <li>Latest Developments</li>
    <li>How To Get There</li>
    <li>Gallery</li>
    <li>Contact Us</li>
    <li>Our Blog</li>
  </ul>
</nav>

<aside class="updates">
  <h2>Tusk Hollow Updates</h2>
  <h3>Project Development</h3>
  <p>The 2nd phase commenced in February 2011 and consists of:-<br>Construction of an international 18 hole golf course by Banda &amp; Lowell, renowned golf course designers from South Africa. front 9 and driving range completed by December 2011 together with the Lirundu golf club house, the back 9 completed by December 2012.<br>20 new executive rooms completed by December 2011<br>A stunning 700 million liter dam for fishing and recreational activities completed by September 2011</p>
  <span class="more">more »</span>
  <h3>Safari</h3>
  <p>We have supplemented our game park with indigenous Malawi wild life which consists of sable, waterbuck, zebra, impala, wildebeest, nyala, giraffe and numerous duiker and smaller wild cats and otters. we have recently introduced from Zambia new breeding stock of roan, kudu and eland and thus now have, in the sanctuary, the “big five” of the antelope family. Bird life is prolific as are the wild flowers and shrubs including massive Mbawa trees and Chiwali palms.</p>
  <span class="more">more »</span>
</aside>

<footer class="site-footer">
  <p>2011 © www.tuskhollowlodge-mw.example | All rights reserved</p>
</footer>
</body>
</html>
```